High-End Print/Digital Ad for Unique Luxury Travel Company Required

Objective:
Design a compelling and visually striking advertisement that highlights our company’s unmatched luxury travel experiences. The ad should elevate our brand image, spark curiosity, and drive prospective clients to contact us.
Target Audience:
• Affluent individuals seeking extraordinary, tailor-made travel experiences
• Affluent, luxury, high-net-worth individuals looking for value, expertise, and white-glove service
• Professionals or retirees who appreciate unique, thoughtfully curated travel over mainstream tourism
Key Messages to Communicate:
• One-of-a-kind luxury travel: Once-in-a-lifetime experiences that are curated with creativity and meticulous attention to detail
• Exceptional service: White-glove, personalized planning from start to finish
• 38 years’ travel experience – expert knowledge of destinations, modes of travel, premium accommodations and well-established, meaningful industry connections.
• Highly trusted: Cruise line executives often say, “No one does what you do.”
Tone and Style:
• Elegant, luxurious, sophisticated
• Eye-catching, polished, and modern
• Professional but warm—conveys trust and credibility
• High-impact visuals (full-bleed imagery, custom graphics, or high-end photography)
Deliverables:
• One full-page print ad and digital ad
• Ready-to-print, high-resolution file + working file (PSD, AI, etc.)
Optional: Social media-optimized version or short motion-graphic variation (if designer offers it)
Inspiration & Visual Style Suggestions:
• Think Lumen Voyages, Harrow Pike Wanderer, Silver Quill, or Orvel Retreats ad styles
• Large, emotive imagery with elegant typography
• Clean layout that speaks luxury, clarity, and trust
Copy Direction (draft):
For those who’ve explored the world—and crave something beyond the ordinary.
Each journey is a masterfully curated experience, rich in detail, seamless in execution, and unforgettable in every way.
Founded in 1997, Tidewell Journeys is a unique travel company specializing in cruising, all-inclusive luxury properties, and tours world-wide for individuals, groups, and incentives.
We offer an exceptional range of services designed to ensure every journey is flawlessly executed and truly unforgettable.
Let us help you plan your next extraordinary adventure.
Note: You may refine the copy slightly based on layout or format needs.
Other Resources for References:
1. Website - www.tidewelljourneys-example.com

```html
<!DOCTYPE html>
<html lang="en">
<head>
<meta charset="utf-8">
<title>Luxury Reimagined — Tidewell Journeys</title>
<link rel="stylesheet" href="https://fonts.googleapis.com/css2?family=DM+Serif+Display&family=Poppins:wght@400;600;700&display=swap">
<style>
  :root {
    --page: #ffffff;
    --sky-top: #8c5a2e;
    --sky-mid: #c97818;
    --sky-low: #6a3208;
    --night: #050302;
    --sun: #fff3c4;
    --accent: #ffe600;
    --ink: #ffffff;
  }
  * { margin: 0; padding: 0; box-sizing: border-box; }
  html, body { width: 1040px; height: 1200px; overflow: hidden; background: var(--page); }
  .ad {
    position: absolute; left: 56px; top: 0; width: 928px; height: 1200px;
    overflow: hidden; color: var(--ink);
    font-family: "Poppins", sans-serif;
  }
  .ad__scene {
    position: absolute; inset: 0;
    background:
      radial-gradient(circle at 522px 621px, var(--sun) 0, rgba(255,220,120,.75) 28px, rgba(240,150,40,.35) 110px, rgba(240,150,40,0) 260px),
      linear-gradient(180deg, var(--sky-top) 0%, var(--sky-mid) 38%, #a85410 60%, var(--sky-low) 72%, #1c0c03 86%, var(--night) 100%);
  }
  .headline { position: absolute; left: 0; width: 100%; text-align: center; font-family: "DM Serif Display", serif; font-weight: 400; line-height: 1; }
  .headline--luxury { top: 58px; font-size: 172px; color: var(--accent); letter-spacing: -2px; }
  .headline--reimagined { top: 178px; font-size: 128px; color: var(--ink); letter-spacing: -2px; }
  .subhead {
    position: absolute; top: 318px; left: 0; width: 100%; text-align: center;
    font-family: "DM Serif Display", serif; font-size: 28px; line-height: 34px; color: var(--ink);
  }
  .feature { position: absolute; left: 72px; width: 380px; }
  .feature__title {
    display: flex; align-items: center; gap: 8px;
    font-weight: 700; font-size: 22px; color: var(--accent); letter-spacing: -.2px; line-height: 26px;
  }
  .feature__title svg { width: 21px; height: 21px; flex: none; }
  .feature__text { margin-left: 33px; margin-top: 4px; font-size: 15.5px; line-height: 19.5px; }
  .feature--trust { top: 725px; }
  .feature--bespoke { top: 841px; }
  .feature--service { top: 950px; }
  .testimonial { position: absolute; left: 598px; top: 804px; width: 280px; text-align: center; }
  .testimonial__mark { display: block; margin: 0 auto; width: 42px; height: 30px; }
  .testimonial__quote { margin-top: 10px; font-size: 37px; line-height: 43px; font-weight: 400; }
  .testimonial__source { margin-top: 10px; font-size: 18.5px; color: var(--accent); }
  .testimonial__mark--close { margin-top: 10px; }
  .brand {
    position: absolute; left: 72px; top: 1086px; width: 320px; text-align: center;
    font-family: "DM Serif Display", serif; font-size: 31px; color: var(--ink); letter-spacing: .5px;
  }
  .cta { position: absolute; left: 440px; top: 1083px; width: 450px; text-align: center; }
  .cta__line { font-size: 17px; letter-spacing: .2px; line-height: 22px; }
  .cta__contact {
    margin-top: 4px; display: flex; justify-content: center; align-items: center; gap: 6px;
    font-weight: 700; font-size: 14.5px; color: var(--accent);
  }
  .cta__contact svg { width: 15px; height: 15px; }
  .cta__divider { width: 1px; height: 13px; background: rgba(255,255,255,.5); margin: 0 6px; }
</style>
</head>
<body>
<svg width="0" height="0" style="position:absolute">
  <defs>
    <symbol id="badge-check" viewBox="0 0 24 24">
      <path fill="#fff" d="M12 1l2.6 2.2 3.4-.3.8 3.3 3 1.7-1.3 3.1 1.3 3.1-3 1.7-.8 3.3-3.4-.3L12 23l-2.6-2.2-3.4.3-.8-3.3-3-1.7L3.5 13 2.2 9.9l3-1.7.8-3.3 3.4.3z"/>
      <path d="M7.5 12.2l3 3 6-6.2" fill="none" stroke="#3a1c06" stroke-width="2.4" stroke-linecap="round" stroke-linejoin="round"/>
    </symbol>
  </defs>
</svg>

<main class="ad">
  <div class="ad__scene" role="img" aria-label="Full-bleed photograph of a large tree silhouetted against an amber sunset, sun glowing through its branches"></div>

  <h1>
    <span class="headline headline--luxury">Luxury</span>
    <span class="headline headline--reimagined">Reimagined</span>
  </h1>
  <p class="subhead">Once-in-a-lifetime journeys, designed with vision,<br>trust, and timeless detail.</p>

  <section class="feature feature--trust">
    <h2 class="feature__title"><svg><use href="#badge-check"/></svg>EXPERTISE YOU CAN TRUST</h2>
    <p class="feature__text">38 years of unmatched insight, global<br>connections, and premium access.</p>
  </section>
  <section class="feature feature--bespoke">
    <h2 class="feature__title"><svg><use href="#badge-check"/></svg>BESPOKE EXPERIENCES</h2>
    <p class="feature__text">Impeccably curated adventures<br>crafted with creativity and care.</p>
  </section>
  <section class="feature feature--service">
    <h2 class="feature__title"><svg><use href="#badge-check"/></svg>WHITE-GLOVE SERVICE</h2>
    <p class="feature__text">From first idea to final return, every<br>detail is flawlessly handled.</p>
  </section>

  <blockquote class="testimonial">
    <svg class="testimonial__mark" viewBox="0 0 42 30" aria-hidden="true">
      <path fill="var(--accent)" d="M18 2C9 5 3 11 3 20a8 8 0 1 0 9-8c1-4 4-7 8-8zM39 2c-9 3-15 9-15 18a8 8 0 1 0 9-8c1-4 4-7 8-8z"/>
    </svg>
    <p class="testimonial__quote">No one does<br>what you do</p>
    <p class="testimonial__source">Cruise Line Executive</p>
    <svg class="testimonial__mark testimonial__mark--close" viewBox="0 0 42 30" aria-hidden="true">
      <path fill="var(--accent)" d="M3 28c9-3 15-9 15-18a8 8 0 1 0-9 8c-1 4-4 7-8 8zM24 28c9-3 15-9 15-18a8 8 0 1 0-9 8c-1 4-4 7-8 8z"/>
    </svg>
  </blockquote>

  <p class="brand">Tidewell Journeys</p>

  <footer class="cta">
    <p class="cta__line">LET US CREATE YOUR NEXT UNFORGETTABLE</p>
    <p class="cta__contact">
      <svg viewBox="0 0 16 16" aria-hidden="true"><circle cx="8" cy="8" r="8" fill="#fff"/><path d="M5.2 3.8l1.4 1.9-.8 1c.6 1.3 1.5 2.2 2.8 2.8l1-.8 1.9 1.4-.7 1.5c-3.4-.3-6.4-3.3-6.7-6.7z" fill="#000"/></svg>
      <span>800.555.0142</span>
      <span class="cta__divider"></span>
      <svg viewBox="0 0 16 16" aria-hidden="true"><circle cx="8" cy="8" r="6.5" fill="none" stroke="#fff" stroke-width="1.4"/><ellipse cx="8" cy="8" rx="2.8" ry="6.5" fill="none" stroke="#fff" stroke-width="1.2"/><path d="M1.5 8h13" stroke="#fff" stroke-width="1.2"/></svg>
      <span>www.tidewelljourneys-example.com</span>
    </p>
  </footer>
</main>
</body>
</html>
```